KR Appraisals website redesign

I would like to refresh my existing website of www.krappraisals-example.com with new graphics, look and feel, as well as updated structure and wording. Content and layout changes have been uploaded to this project Brief.

My existing website has a dark feel. I am now looking for a light and energetic feel. Financial Services is my industry, so the website should be reflect that. I would also like to reflect the concepts of Trust, Service and Expertise.

The website must be serious and upmarket.

Target Market(s)

Corporate board members, CFO's, treasurers and controllers
Auditors, tax advisors, private equity and venture capital asset managers, investors, tax authorities

Industry/Entity Type

Financial Service

Coding

Coded - Design and coding required

Number of Pages Required

5+ page

Font styles to use
Sans Serif
Other font styles liked:
• Designer can choose another modern font

Colors
0355a3
3277b5
85acd3
eaf1f7
f37122
f68d4d
9bcb3c
acd037
cadf82

Requirements
Must have
• Good hi resolution pictures that convey "Finance", "Trust", "Service" or "Expertise".
• An anti-bot (such as Captcha) mechanism in the contact form.
Should not have
• Must not have all content on one rolling screen.

```html
<!DOCTYPE html>
<html lang="en">
<head>
<meta charset="utf-8">
<title>KR Appraisals – Our Services</title>
<link href="https://fonts.googleapis.com/css2?family=Nunito:wght@400;600;700;800&display=swap" rel="stylesheet">
<style>
:root{
  --blue-dark:#0355a3;
  --blue:#3277b5;
  --blue-light:#85acd3;
  --blue-pale:#eaf1f7;
  --orange:#f37122;
  --green:#9bcb3c;
  --text:#5a5a5a;
  --nav:#777;
  --panel:#f2f2f2;
  --footer:#333333;
  --footer-text:#9a9a9a;
  --footer-rule:#5a5a5a;
}
*{margin:0;padding:0;box-sizing:border-box}
html,body{width:1200px;height:1084px;overflow:hidden;background:#fff}
body{position:relative;font-family:"Nunito",sans-serif;color:var(--text)}
.site-header{position:absolute;left:0;top:0;width:1200px;height:100px;background:linear-gradient(90deg,#e2e3d9 0%,#e9eadd 45%,#f2f3e2 100%)}
.brand{position:absolute;left:161px;top:36px;display:flex;align-items:center;gap:10px}
.brand-mark{width:22px;height:22px;border:2px solid #8a8a8a}
.brand-name{font-size:21px;font-weight:600;color:#7d7d7d;letter-spacing:.5px}
.main-nav{position:absolute;top:45px;left:611px;display:flex;gap:0}
.main-nav a{font-size:11.5px;font-weight:700;color:var(--nav);text-decoration:none;text-transform:uppercase;position:absolute;white-space:nowrap}
.main-nav a.active{color:var(--blue-dark)}
.page-title{position:absolute;top:184px;left:0;width:1200px;text-align:center;font-size:38px;font-weight:800;color:var(--orange);letter-spacing:-.5px}
.service-panel{position:absolute;left:562px;top:274px;width:477px;height:367px;background:var(--panel)}
.service-image{position:absolute;left:161px;top:311px;width:439px;height:293px;background:linear-gradient(135deg,#b8d4f6 0%,#6fa4e6 45%,#2f6fc9 80%,#1f4f95 100%)}
.service-title{position:absolute;left:646px;top:393px;font-size:30px;font-weight:800;color:var(--green);letter-spacing:-.3px}
.service-text{position:absolute;left:646px;top:442px;width:350px;font-size:10.5px;line-height:19px;color:var(--text)}
.footer-shape{position:absolute;left:0;top:731px}
.footer-brand{position:absolute;left:0;top:788px;width:1200px;display:flex;justify-content:center;align-items:center;gap:10px}
.footer-brand .brand-mark{border-color:#8a8a8a}
.footer-brand .brand-name{color:#8d8d8d}
.footer-rule{position:absolute;left:161px;width:878px;height:1px;background:var(--footer-rule)}
.footer-nav a{position:absolute;top:890px;font-size:11px;font-weight:700;color:#8a8a8a;text-decoration:none;text-transform:uppercase;white-space:nowrap}
.footer-nav a.active{color:var(--green)}
.footer-col{position:absolute;top:948px;font-size:10.5px;color:var(--footer-text)}
.footer-col h3{font-size:13px;font-weight:800;color:var(--orange);margin-bottom:10px;text-transform:uppercase}
.footer-col p{line-height:22.5px}
.footer-col .hl{color:var(--green)}
.footer-col .w{color:#f0f0f0}
.contact-line{position:relative;padding-left:20px;line-height:16.5px}
.contact-line svg{position:absolute;left:1px;top:1px}
.contact-phone{margin-top:13px;color:#f0f0f0;font-size:11.5px;font-weight:700}
.badge{position:absolute;background:#555}
</style>
</head>
<body>
<header class="site-header">
  <div class="brand"><span class="brand-mark"></span><span class="brand-name">KR APPRAISALS</span></div>
  <nav class="main-nav">
    <a style="left:0">Home</a>
    <a style="left:75px">About</a>
    <a class="active" style="left:155px">Services</a>
    <a style="left:250px">News &amp; Views</a>
    <a style="left:374px">Contact</a>
  </nav>
</header>

<h1 class="page-title">OUR SERVICES</h1>

<section class="service">
  <div class="service-panel"></div>
  <div class="service-image" role="img" aria-label="Blue-toned photo of financial charts with a magnifying glass"></div>
  <h2 class="service-title">BUSINESS VALUATION</h2>
  <p class="service-text">Company stakeholders trust KR Appraisals to provide business valuations for transaction, accounting, tax, legal, and share or option participation purposes. Through our bespoke approach and global network, we customize teams to the needs of our clients.</p>
</section>

<footer>
  <svg class="footer-shape" width="1200" height="353" viewBox="0 0 1200 353"><polygon points="0,68 600,0 1200,68 1200,353 0,353" fill="var(--footer)"/></svg>
  <div class="footer-brand"><span class="brand-mark"></span><span class="brand-name">KR APPRAISALS</span></div>
  <div class="footer-rule" style="top:876px"></div>
  <nav class="footer-nav">
    <a class="active" style="left:386px">Home</a>
    <a style="left:461px">About</a>
    <a style="left:541px">Services</a>
    <a style="left:636px">News &amp; Views</a>
    <a style="left:760px">Contact</a>
  </nav>
  <div class="footer-rule" style="top:921px"></div>

  <div class="footer-col" style="left:163px">
    <h3>Credits</h3>
    <p>© 2019 <span class="hl">KR Appraisals</span></p>
    <p>Logo by <span class="w">Mara Lindqvist</span></p>
    <p>Website by <span class="hl">Northfield Webworks</span></p>
  </div>
  <div class="footer-col" style="left:390px">
    <h3>Leiden</h3>
    <p class="contact-line"><svg width="10" height="13" viewBox="0 0 10 13"><path d="M5 0a5 5 0 0 0-5 5c0 3.5 5 8 5 8s5-4.5 5-8a5 5 0 0 0-5-5zm0 7a2 2 0 1 1 0-4 2 2 0 0 1 0 4z" fill="var(--green)"/></svg>Havenweg 140<br>2311 XK Leiden</p>
    <p class="contact-line contact-phone"><svg width="12" height="12" viewBox="0 0 12 12"><path d="M2.5 0l2 3-1.3 1.3a7 7 0 0 0 4.5 4.5L9 7.5l3 2-1.5 2.5C5 12 0 7 0 1.5z" fill="var(--green)"/></svg>070 555 0142</p>
  </div>
  <div class="footer-col" style="left:617px">
    <h3>Amsterdam</h3>
    <p class="contact-line"><svg width="10" height="13" viewBox="0 0 10 13"><path d="M5 0a5 5 0 0 0-5 5c0 3.5 5 8 5 8s5-4.5 5-8a5 5 0 0 0-5-5zm0 7a2 2 0 1 1 0-4 2 2 0 0 1 0 4z" fill="var(--green)"/></svg>Lindenkade 27<br>1075 ZR Amsterdam</p>
    <p class="contact-line contact-phone"><svg width="12" height="12" viewBox="0 0 12 12"><path d="M2.5 0l2 3-1.3 1.3a7 7 0 0 0 4.5 4.5L9 7.5l3 2-1.5 2.5C5 12 0 7 0 1.5z" fill="var(--green)"/></svg>020 555 0187</p>
  </div>

  <div class="badge" role="img" aria-label="Professional membership badge" style="left:856px;top:941px;width:170px;height:36px;border-radius:4px"></div>
  <div class="badge" role="img" aria-label="Professional membership badge" style="left:854px;top:988px;width:170px;height:70px;border-radius:4px"></div>
</footer>
</body>
</html>
```